The Brandwell Firm

We need a new design for our letterhead and envelopes. We are a personal injury and criminal defense firm so we need something modern and clean, but more on the professional/traditional side. Our new logo has two colors and is attached to the file so we need something that works well with those colors/matches the design. The following information needs to be on the letterhead:
Phone: (555) 214-3370
Fax: (555) 214-5186
Toll-Free: (888) 431-2059
Post Office Box 4721
Millbrook, SC 29555-4721
HarmClaimCounsel.example
PalmettoTrialAdvocates.example

Target Market(s)

Clients, government agencies, other law firms

Industry/Entity Type

Legal

Font styles to use
Sans Serif
Other font styles liked:
• Arial

Colors

Designer to choose colors to be used in the design.

Requirements
Must have
• Must look professional and clean, modern
Nice to have
• I would like to see a design that works with the logo but does not distract from the content that will be printed on it
Should not have
• Too many colors or crazy designs.

```html
<!DOCTYPE html>
<html lang="en">
<head>
<meta charset="utf-8">
<title>The Brandwell Firm — Stationery</title>
<link rel="stylesheet" href="https://fonts.googleapis.com/css2?family=Open+Sans:wght@400;600;700&display=swap">
<style>
  :root {
    --navy: #2d2c87;
    --red: #c81f2a;
    --paper: #efefef;
    --ink: #4a4a4a;
    --ink-soft: #6d6d6d;
    --backdrop: #d4d4d4;
  }
  * { box-sizing: border-box; margin: 0; padding: 0; }
  html, body { width: 1200px; height: 810px; overflow: hidden; }
  body {
    background: var(--backdrop);
    font-family: "Open Sans", Arial, sans-serif;
    position: relative;
  }
  .sheet { position: absolute; background: var(--paper); overflow: hidden; }

  /* Letterhead */
  .letterhead { left: 137px; top: 110px; width: 436px; height: 614px; }
  .brand { position: absolute; display: flex; align-items: center; gap: 7px; }
  .brand-dot { width: 14px; height: 14px; border-radius: 50%; background: var(--red); flex: none; }
  .brand-name {
    font-weight: 700; color: var(--navy); text-transform: uppercase;
    letter-spacing: .04em; line-height: 1.05;
  }
  .letterhead .brand { left: 38px; top: 70px; }
  .letterhead .brand-name { font-size: 17px; }

  .contact { position: absolute; left: 308px; top: 56px; font-size: 7.3px; line-height: 9.3px; color: var(--ink); }
  .contact-lines { display: grid; grid-template-columns: 34px 8px auto; margin-top: 6px; }
  .contact-label { color: var(--navy); font-weight: 600; }

  .recipient { position: absolute; left: 38px; top: 208px; font-size: 7.6px; line-height: 11.5px; color: var(--ink-soft); }
  .body-copy { position: absolute; left: 38px; width: 362px; font-size: 7.4px; line-height: 11.4px; color: var(--ink-soft); text-align: justify; }
  .body-copy.first { top: 276px; }
  .body-copy.second { top: 378px; }

  .signature { position: absolute; left: 38px; top: 443px; width: 84px; height: 52px;
    background: linear-gradient(135deg, rgba(45,44,135,.18), rgba(45,44,135,.06)); border-radius: 4px; }
  .sign-title { position: absolute; left: 37px; top: 507px; font-size: 7.4px; color: var(--ink-soft); }

  .swoosh { position: absolute; left: 0; bottom: 0; display: block; }
  .footer-links { position: absolute; bottom: 10px; right: 37px; font-size: 7.4px; color: #fff; letter-spacing: .01em; }
  .footer-links .sep { margin: 0 6px; }

  /* Envelope back */
  .envelope-back { left: 619px; top: 194px; width: 444px; height: 221px; }
  .flap { position: absolute; left: 0; top: 0; display: block; }

  /* Envelope front */
  .envelope-front { left: 618px; top: 444px; width: 445px; height: 221px; }
  .envelope-front .brand { left: 24px; top: 44px; }
  .envelope-front .brand-name { font-size: 17px; }
  .return-address { position: absolute; left: 24px; top: 105px; font-size: 7.3px; line-height: 9.5px; color: var(--ink); }
  .envelope-front .footer-links { bottom: 8px; right: 34px; }
</style>
</head>
<body>

<section class="sheet letterhead" aria-label="Letterhead">
  <div class="brand">
    <span class="brand-dot"></span>
    <span class="brand-name">The Brandwell Firm</span>
  </div>

  <div class="contact">
    <p>Post Office Box 4721</p>
    <p>Millbrook, SC 29555-4721</p>
    <div class="contact-lines">
      <span class="contact-label">Phone</span><span>:</span><span>(555) 214-3370</span>
      <span class="contact-label">Fax</span><span>:</span><span>(555) 214-5186</span>
      <span class="contact-label">Toll-Free</span><span>:</span><span>(888) 431-2059</span>
    </div>
  </div>

  <div class="recipient">
    <p>Dear Halvorsen</p>
    <p>Tarrow Print Works Corporation</p>
    <p>Department Design</p>
  </div>

  <p class="body-copy first">Lorem ipsum dolor sit amet, consectetuer adipiscing elit. Aenean commodo ligula eget dolor. Aenean massa. Cum sociis natoque penatibus et magnis dis parturient montes, nascetur ridiculus mus. Donec quam felis, ultricies nec, pellentesque eu, pretium quis, sem. Nulla consequat massa quis enim. Donec pede justo, fringilla vel, aliquet nec, vulputate eget, arcu. In enim justo, rhoncus ut, imperdiet a, venenatis vitae, justo. Nullam dictum felis eu pede mollis pretium. Integer tincidunt. Cras dapibus. Vivamus elementum semper nisi.Nullam dictum felis eu pede mollis pretium. Integer tincidunt. Cras dapibus. Vivamus elementum semper nisi.felis eu pede mollis pretium. Integer tincidunt. Cras dapibus.</p>

  <p class="body-copy second">Quisque rutrum. Aenean imperdiet. Etiam ultricies nisi vel augue. Curabitur ullamcorper ultricies nisi. Nam eget dui. Etiam rhoncus. Maecenas tempus, tellus eget condimentum rhoncus, sem quam semper libero, sit amet adipiscing sem neque sed ipsum.felis pede mollis pretium. I am tincidunt. Cras dapibus.</p>

  <div class="signature" role="img" aria-label="Handwritten signature of the director"></div>
  <p class="sign-title">Director/Excecutive Director</p>

  <svg class="swoosh" width="436" height="40" viewBox="0 0 436 40" aria-hidden="true">
    <path d="M0 16 Q170 0 320 1 Q180 4 0 22 Z" fill="var(--red)"/>
    <path d="M0 29 Q190 6 436 12 L436 40 L0 40 Z" fill="var(--navy)"/>
  </svg>
  <p class="footer-links">www.HarmClaimCounsel.example<span class="sep">|</span>www.PalmettoTrialAdvocates.example</p>
</section>

<section class="sheet envelope-back" aria-label="Envelope back">
  <svg class="flap" width="444" height="66" viewBox="0 0 444 66" aria-hidden="true">
    <path d="M0 0 L444 0 L436 54 Q434 65 422 65 L22 65 Q10 65 8 54 Z" fill="var(--navy)"/>
  </svg>
</section>

<section class="sheet envelope-front" aria-label="Envelope front">
  <div class="brand">
    <span class="brand-dot"></span>
    <span class="brand-name">The Brandwell Firm</span>
  </div>
  <div class="return-address">
    <p>Post Office Box 4721</p>
    <p>Millbrook, SC 29555-4721</p>
  </div>

  <svg class="swoosh" width="445" height="34" viewBox="0 0 445 34" aria-hidden="true">
    <path d="M0 14 Q180 0 330 1 Q190 4 0 20 Z" fill="var(--red)"/>
    <path d="M0 25 Q200 4 445 10 L445 34 L0 34 Z" fill="var(--navy)"/>
  </svg>
  <p class="footer-links">www.HarmClaimCounsel.example<span class="sep">|</span>www.PalmettoTrialAdvocates.example</p>
</section>

</body>
</html>
```